Design 4 pages for an event discovery website

This is a contest for the design of 4 pages for an events discovery website. The feature is part of the new sign-up process.

Please see the attached document for a full scope, mockups and the parent category icons.

Target Market(s)

18-35 Australian event goers

Industry/Entity Type

Events

Number of Pages Required

4 page

```html
<!DOCTYPE html>
<html lang="en">
<head>
<meta charset="utf-8">
<title>Qurovent – Step 1 of 5</title>
<link rel="stylesheet" href="https://fonts.googleapis.com/css2?family=Open+Sans:wght@400;600;700&display=swap">
<style>
  :root {
    --teal: #5bbcbc;
    --brand: #14a0a3;
    --header-bg: #ffffff;
    --top-rule: #9a9a9a;
    --search-bg: #efefef;
    --search-text: #8a8a8a;
    --hero-deep: #141518;
    --hero-mid: #24262c;
    --hero-glow: #3a3128;
    --text-light: #ffffff;
    --tick: #d6d6d6;
    --footer-bg: #1c1c1c;
    --footer-text: #a3a3a3;
    --chirp-a: #2fd0f5; --chirp-b: #0fa9e0;
    --snap-a: #4c4c4c; --snap-b: #232323;
    --tune-a: #f4b077; --tune-b: #e48d4b;
    --melody-a: #2cc2c2; --melody-b: #129d9f;
    --social-1: #3b5a9a; --social-2: #2aa6e0; --social-3: #3b3b3b; --social-4: #cc2127;
  }
  * { box-sizing: border-box; margin: 0; padding: 0; }
  html, body { width: 1200px; height: 701px; overflow: hidden; }
  body { font-family: "Open Sans", Arial, sans-serif; background: var(--hero-deep); position: relative; }

  .site-header {
    position: absolute; top: 0; left: 0; width: 1200px; height: 111px;
    background: var(--header-bg); border-top: 3px solid var(--top-rule);
  }
  .brand {
    position: absolute; left: 99px; top: 30px;
    display: flex; align-items: center; gap: 8px;
    font-weight: 700; font-size: 32px; color: var(--brand); letter-spacing: 0.5px;
  }
  .brand-mark { width: 14px; height: 14px; background: var(--brand); }
  .search {
    position: absolute; left: 779px; top: 29px; width: 173px; height: 33px;
    background: var(--search-bg); border-radius: 3px;
    font-size: 11px; color: var(--search-text); padding: 9px 0 0 12px;
  }
  .search svg { position: absolute; right: 10px; top: 9px; }
  .auth-btn {
    position: absolute; top: 29px; height: 33px; background: var(--teal);
    color: var(--text-light); font-size: 13px; font-weight: 600; border-radius: 3px;
    display: flex; align-items: center; justify-content: center;
  }
  .auth-signup { left: 959px; width: 67px; }
  .auth-login { left: 1033px; width: 67px; }

  .hero {
    position: absolute; top: 111px; left: 0; width: 1200px; height: 521px;
    background:
      radial-gradient(ellipse at 40% 85%, var(--hero-glow) 0%, transparent 55%),
      radial-gradient(ellipse at 75% 40%, #2a2c33 0%, transparent 50%),
      linear-gradient(180deg, var(--hero-deep) 0%, var(--hero-mid) 60%, #1a1a1d 100%);
  }
  .step-title {
    position: absolute; left: 99px; top: 170px;
    font-size: 31px; font-weight: 400; color: var(--text-light); letter-spacing: 0.5px;
  }
  .step-lead { position: absolute; left: 99px; font-size: 14.5px; color: var(--text-light); }
  .lead-1 { top: 220px; }
  .lead-2 { top: 247px; }

  .connect {
    position: absolute; left: 99px; width: 246px; height: 45px; border-radius: 2px;
    display: flex; align-items: center; color: var(--text-light);
    font-size: 19.5px; font-weight: 600;
  }
  .connect-icon {
    width: 55px; height: 100%; display: flex; align-items: center; justify-content: center;
    border-right: 1px solid rgba(0,0,0,0.18);
  }
  .connect-icon span { width: 22px; height: 22px; border-radius: 50%; background: var(--text-light); }
  .connect-label { padding-left: 22px; }
  .chirp { top: 291px; background: linear-gradient(var(--chirp-a), var(--chirp-b)); }
  .snap { top: 348px; background: linear-gradient(var(--snap-a), var(--snap-b)); }
  .tune { top: 407px; background: linear-gradient(var(--tune-a), var(--tune-b)); }
  .melody { top: 465px; background: linear-gradient(var(--melody-a), var(--melody-b)); }

  .status {
    position: absolute; left: 365px; display: flex; align-items: center; gap: 10px;
    color: var(--text-light); font-size: 13.5px;
  }
  .status-linked { top: 307px; }
  .status-requested { top: 425px; }

  .site-footer {
    position: absolute; top: 632px; left: 0; width: 1200px; height: 69px; background: var(--footer-bg);
  }
  .copyright { position: absolute; left: 99px; top: 26px; font-size: 12px; color: var(--footer-text); }
  .copyright strong { color: var(--text-light); font-weight: 400; }
  .social { position: absolute; top: 20px; width: 28px; height: 28px; border-radius: 50%; }
  .s1 { left: 970px; background: var(--social-1); }
  .s2 { left: 1004px; background: var(--social-2); }
  .s3 { left: 1038px; background: var(--social-3); }
  .s4 { left: 1073px; background: var(--social-4); }
  .page-code { position: absolute; left: 1129px; top: 32px; font-size: 11px; color: var(--text-light); }
</style>
</head>
<body>
  <header class="site-header">
    <div class="brand"><span class="brand-mark"></span>QUROVENT</div>
    <div class="search">Search
      <svg width="14" height="14" viewBox="0 0 14 14"><circle cx="5.5" cy="5.5" r="4.2" fill="none" stroke="#a0a0a0" stroke-width="2"/><line x1="8.6" y1="8.6" x2="13" y2="13" stroke="#a0a0a0" stroke-width="2.4" stroke-linecap="round"/></svg>
    </div>
    <div class="auth-btn auth-signup">SIGNUP</div>
    <div class="auth-btn auth-login">LOGIN</div>
  </header>

  <main class="hero" role="img" aria-label="Night-time city skyline with lit towers and light trails on a freeway"></main>

  <h1 class="step-title">STEP 1 OF 5</h1>
  <p class="step-lead lead-1">Link in all your other Social media accounts and Music players</p>
  <p class="step-lead lead-2">By Linking your accounts, we can save you a lot of time by automactically determing your intrests</p>

  <div class="connect chirp"><div class="connect-icon"><span></span></div><div class="connect-label">chirpline</div></div>
  <div class="connect snap"><div class="connect-icon"><span></span></div><div class="connect-label">snapframe</div></div>
  <div class="connect tune"><div class="connect-icon"><span></span></div><div class="connect-label">Tunewave</div></div>
  <div class="connect melody"><div class="connect-icon"><span></span></div><div class="connect-label">melodybox</div></div>

  <div class="status status-linked">
    <svg width="20" height="16" viewBox="0 0 20 16"><path d="M2 8.5 L7.5 14 L18 2.5" fill="none" stroke="var(--tick)" stroke-width="3.6" stroke-linecap="round" stroke-linejoin="round"/></svg>
    Linked
  </div>
  <div class="status status-requested">
    <svg width="20" height="16" viewBox="0 0 20 16"><path d="M2 8.5 L7.5 14 L18 2.5" fill="none" stroke="var(--tick)" stroke-width="3.6" stroke-linecap="round" stroke-linejoin="round"/></svg>
    &nbsp;We don't have that future yet but have requested your interest
  </div>

  <footer class="site-footer">
    <p class="copyright">Copyright &copy; 2015 <strong>Qurovent</strong>. All rights reserved</p>
    <span class="social s1"></span>
    <span class="social s2"></span>
    <span class="social s3"></span>
    <span class="social s4"></span>
    <span class="page-code">C1</span>
  </footer>
</body>
</html>
```